Holistic Health Coach needs simple web site design for a new practice

I need a web (re)design for my entire site, Ridgeway Fern Lady. I have a beautiful new blue and green logo that I'd like the site fonts and color scheme to be built around. I'll attach my new logo so you'll know the colors/design feel I'm after.

I want easy navigation for my mostly text based site, widgets for my social media pages and a clean, fun, light feel for the site.

Target Market(s)

People looking to take charge of their own health, and who may need my coaching services to obtain optimal wellness.

Industry/Entity Type

Health

Coding

Coded - Design and coding required

Number of Pages Required

5+ page

Font styles to use
Script

Colors
33b8a4
33a6d7
ffffff

Requirements
Must have
• Must incorporate my logo design, as well as same/similar fonts and color scheme.
• I'd like it to stay as close to the current design as possible.
Nice to have
• Would love to incorporate a hover over menu (for example, when a user hovers over "About", they will see the submenu in a floating design.
Should not have
• No dark colors or masculine feel

```html
<!DOCTYPE html>
<html lang="en">
<head>
<meta charset="utf-8">
<title>Ridgeway Fern Lady</title>
<link href="https://fonts.googleapis.com/css2?family=Arvo:wght@400;700&family=Open+Sans:wght@400;600&family=Raleway:wght@400;500;600&family=Roboto:wght@400;500&display=swap" rel="stylesheet">
<style>
:root{
  --green:#72bf2a;
  --green-dark:#5fa81e;
  --blue:#1a8fd1;
  --ink:#2b2b2b;
  --body:#4a4a4a;
  --muted:#8a8a8a;
  --card:#f1f0f0;
  --btn:#363636;
  --pink:#e985bb;
  --footer:#1d1d1d;
  --white:#ffffff;
}
*{box-sizing:border-box;margin:0;padding:0}
html,body{width:1200px;height:2314px;overflow:hidden}
body{position:relative;background:var(--white);font-family:"Open Sans",sans-serif;color:var(--body)}
.abs{position:absolute}

/* header */
.site-header{left:0;top:0;width:1200px;height:92px;background:var(--white);border-bottom:1px solid #e6e6e6}
.brand{left:76px;top:28px;display:flex;align-items:center;gap:10px;font-family:"Raleway",sans-serif;font-weight:600;font-size:25px;color:var(--green);letter-spacing:.3px}
.brand-dot{width:14px;height:14px;border-radius:50%;background:var(--blue)}
.main-nav{top:50px;left:0;width:1200px;font-family:"Raleway",sans-serif;font-size:12.5px;font-weight:500;color:var(--ink);text-transform:uppercase}
.main-nav span{position:absolute;white-space:nowrap}
.main-nav .active{color:var(--green)}
.submenu{left:460px;top:88px;width:171px;height:194px;background:var(--green);padding:10px 12px;z-index:5}
.submenu::before{content:"";position:absolute;left:75px;top:-8px;border:8px solid transparent;border-top:0;border-bottom-color:var(--green)}
.submenu li{list-style:none;font-family:"Open Sans",sans-serif;font-size:11.5px;color:var(--white);height:29.5px;line-height:29px;border-bottom:1px solid rgba(255,255,255,.25);padding-left:12px;position:relative}
.submenu li:last-child{border-bottom:0}
.submenu li::before{content:"";position:absolute;left:3px;top:13px;width:4px;height:4px;border-radius:50%;background:var(--white)}

/* hero */
.hero{left:0;top:92px;width:1200px;height:460px;background:linear-gradient(180deg,#e9eef0 0%,#d6dfe2 45%,#b8c49a 78%,#c7b86a 100%)}
.hero-arrow{width:62px;height:62px;border-radius:50%;background:rgba(60,60,60,.45);top:290px}

/* articles */
.section-title{font-family:"Arvo",serif;font-size:27px;color:var(--ink);font-weight:400}
.article{left:74px;width:773px;height:225px;background:var(--card)}
.article-thumb{position:absolute;left:17px;top:21px;width:227px;height:145px}
.article-body{position:absolute;left:270px;top:22px;width:480px}
.article-title{font-family:"Roboto",sans-serif;font-weight:500;font-size:18.5px;line-height:23px;color:var(--blue)}
.article-meta{margin-top:6px;font-size:11px;color:var(--muted);display:flex;gap:22px;align-items:center}
.article-meta svg{vertical-align:-2px;margin-right:4px}
.article-excerpt{margin-top:10px;font-size:11.4px;line-height:20.5px;color:var(--body)}
.read-more{position:absolute;left:271px;bottom:18px;width:116px;height:28px;background:var(--btn);color:var(--white);font-family:"Raleway",sans-serif;font-weight:600;font-size:11px;text-align:center;line-height:28px;letter-spacing:.5px}

/* sidebar */
.sidebar-title{font-family:"Arvo",serif;font-size:24px;color:var(--ink)}
.recent{left:884px;width:242px;display:flex;gap:18px}
.recent-thumb{width:88px;height:74px;flex:none}
.recent p{font-size:11.3px;line-height:21px;text-align:justify;color:var(--body)}
.view-all{left:884px;top:957px;width:105px;height:28px;background:var(--pink);color:var(--white);font-family:"Raleway",sans-serif;font-size:11px;font-weight:600;text-align:center;line-height:28px}
.rule{left:884px;top:1012px;width:242px;height:1px;background:#e4e4e4}
.signup{left:884px;top:1045px;width:242px;height:415px;background:var(--green);color:var(--white);padding:22px 18px}
.signup h3{font-family:"Arvo",serif;font-weight:400;font-size:24px;text-align:center;letter-spacing:1px}
.signup .sub{font-family:"Raleway",sans-serif;font-weight:600;font-size:11.5px;text-align:center;margin-top:2px}
.signup .lede{font-size:11.5px;line-height:19px;text-align:center;margin-top:14px}
.signup label{display:block;font-size:11.5px;margin-top:16px}
.signup .field{margin-top:6px;height:31px;background:var(--white);color:#888;font-style:italic;font-size:11.5px;line-height:31px;padding-left:12px;margin-left:0;width:207px}
.signup .submit{margin-top:20px;height:42px;background:#1f1f1f;text-align:center;line-height:42px;font-family:"Raleway",sans-serif;font-weight:600;font-size:14px;width:207px}
.feed-title{left:884px;top:1500px;width:242px;font-family:"Arvo",serif;font-size:15.5px;line-height:22px;color:var(--ink);text-transform:uppercase}
.feed-grid{left:884px;top:1562px;display:grid;grid-template-columns:repeat(4,52px);gap:8px}
.feed-grid div{width:52px;height:52px}
.feed-btn{top:1696px;height:25px;background:#d52b2b;color:var(--white);font-size:10.5px;line-height:25px;text-align:center;border-radius:2px}
.accordion{left:885px;width:233px;height:38px;background:#3a3a3a;color:var(--white);font-family:"Raleway",sans-serif;font-weight:600;font-size:11.5px;line-height:38px;padding-left:20px;text-transform:uppercase}
.accordion svg{position:absolute;right:16px;top:15px}

/* footer */
.site-footer{left:0;top:2162px;width:1200px;height:152px;background:var(--footer)}
.social{top:2197px;width:38px;height:38px;border-radius:50%}
.copyright{left:77px;top:2260px;font-size:11px;color:#9a9a9a}
.footer-news{left:870px;top:2202px;font-family:"Raleway",sans-serif;font-size:14px;color:var(--white);letter-spacing:.3px}
.footer-input{left:870px;top:2241px;width:220px;height:32px;border:1px solid #555;background:#151515;color:#888;font-size:11px;line-height:30px;padding-left:14px;font-style:italic}
.footer-go{left:1090px;top:2241px;width:34px;height:32px;background:#555}
</style>
</head>
<body>

<header class="site-header abs">
  <div class="brand abs"><span class="brand-dot"></span>Ridgeway Fern Lady</div>
  <nav class="main-nav abs">
    <span style="left:436px">Home</span>
    <span class="active" style="left:509px">About Maren</span>
    <span style="left:623px">Articles</span>
    <span style="left:728px">Essential Oils</span>
    <span style="left:865px">21-Day Sweet Reset Coaching Services</span>
  </nav>
</header>

<section class="hero abs" role="img" aria-label="Photo of a woman running outdoors in a sunny field with a city skyline behind her"></section>
<div class="hero-arrow abs" style="left:92px">
  <svg width="62" height="62" viewBox="0 0 62 62"><path d="M34 23l-8 8 8 8" fill="none" stroke="#fff" stroke-width="2.5"/></svg>
</div>
<div class="hero-arrow abs" style="left:1044px">
  <svg width="62" height="62" viewBox="0 0 62 62"><path d="M28 23l8 8-8 8" fill="none" stroke="#fff" stroke-width="2.5"/></svg>
</div>

<ul class="submenu abs">
  <li>Neque porro</li>
  <li>Quisquam est qui</li>
  <li>Dolorem ipsum quia</li>
  <li>Dolor sit amet, con</li>
  <li>Sectetur, adipisci</li>
  <li>Velit Adiplicsete</li>
</ul>

<h2 class="section-title abs" style="left:76px;top:592px">Articles</h2>

<article class="article abs" style="top:637px">
  <div class="article-thumb" role="img" aria-label="Illustration of a red apple with a medical cross" style="background:radial-gradient(circle at 50% 50%,#b8202a 0 28%,#ffffff 30%)"></div>
  <div class="article-body">
    <h3 class="article-title">Lifestyles of the Tired and Wired – Module 4 of Root Reset: Adrenal Fatigue</h3>
    <div class="article-meta"><span><svg width="11" height="11"><rect x="1" y="2" width="9" height="8" fill="none" stroke="#999"/></svg>April 10, 2015</span><span><svg width="12" height="11"><ellipse cx="6" cy="5" rx="5" ry="4" fill="none" stroke="#999"/></svg>Leave a comment</span></div>
    <p class="article-excerpt">As the title suggests, Module 4 of Root Reset: Adrenal Fatigue is all about lifestyle factors. Specifically, how you can make changes to your lifestyle in the areas of stress, sleep, social connection, and exercise and recovery.</p>
  </div>
  <div class="read-more">READ MORE</div>
</article>

<article class="article abs" style="top:882px">
  <div class="article-thumb" role="img" aria-label="Pink card listing the dates of the April class series" style="background:#f4b5bf"></div>
  <div class="article-body">
    <h3 class="article-title">April Essential Living Education Series</h3>
    <div class="article-meta"><span><svg width="11" height="11"><rect x="1" y="2" width="9" height="8" fill="none" stroke="#999"/></svg>April 10, 2015</span><span><svg width="12" height="11"><ellipse cx="6" cy="5" rx="5" ry="4" fill="none" stroke="#999"/></svg>Leave a comment</span></div>
    <p class="article-excerpt">During the month of April, I will be doing a series of Circle classes designed with you in mind. Topics range from skin care and personal care to Healing Oils of the Ancients, Hormones, and how to have a Chemical Free Home. I hope you can join me for some fun educational Circle classes!! Please let me know what other classes you'd like to see :)</p>
  </div>
  <div class="read-more">READ MORE</div>
</article>

<article class="article abs" style="top:1130px">
  <div class="article-thumb" role="img" aria-label="Diagram of the pregnenolone steal hormone pathway" style="background:linear-gradient(180deg,#ffffff 0%,#eef2f8 40%,#c9d5ea 100%)"></div>
  <div class="article-body">
    <h3 class="article-title">Module 3: A Nice Supplement to the Program</h3>
    <div class="article-meta"><span><svg width="11" height="11"><rect x="1" y="2" width="9" height="8" fill="none" stroke="#999"/></svg>April 10, 2015</span><span><svg width="12" height="11"><ellipse cx="6" cy="5" rx="5" ry="4" fill="none" stroke="#999"/></svg>Leave a comment</span></div>
    <p class="article-excerpt">Sorry this is a day late. I'm on Day 2 without coffee, and I finally feel like myself again :) Module 3 is all about supplementation to support your body as it repairs itself from the effects of HPA Axis dysregulation. The lessons this week focus on two types of supplementation: general supplementation and adrenal fatigue level supplementation.</p>
  </div>
  <div class="read-more">READ MORE</div>
</article>

<article class="article abs" style="top:1377px">
  <div class="article-thumb" role="img" aria-label="Promotional graphic with a cup of herbal coffee on a wooden table" style="background:linear-gradient(180deg,#f3efe6 0%,#e2d6bf 55%,#3d8aa8 100%)"></div>
  <div class="article-body">
    <h3 class="article-title">What Do You Mean I Can't Have Coffee?!? – Module 2 Root Reset: Adrenal Fatigue</h3>
    <div class="article-meta"><span><svg width="11" height="11"><rect x="1" y="2" width="9" height="8" fill="none" stroke="#999"/></svg>April 10, 2015</span><span><svg width="12" height="11"><ellipse cx="6" cy="5" rx="5" ry="4" fill="none" stroke="#999"/></svg>Leave a comment</span></div>
    <p class="article-excerpt">As the title suggests, Module 4 of Root Reset: Adrenal Fatigue is all about lifestyle factors. Specifically, how you can make changes to your lifestyle in the areas of stress, sleep, social connection, and exercise and recovery.</p>
  </div>
  <div class="read-more">READ MORE</div>
</article>

<article class="article abs" style="top:1627px">
  <div class="article-thumb" role="img" aria-label="Photo of a row of essential oil bottles on a wooden surface" style="background:linear-gradient(180deg,#eceaea 0%,#d9d4d2 55%,#a98e74 100%)"></div>
  <div class="article-body">
    <h3 class="article-title">What Do You Mean I Can't Have Coffee?!? – Module 2 Root Reset: Adrenal Fatigue</h3>
    <div class="article-meta"><span><svg width="11" height="11"><rect x="1" y="2" width="9" height="8" fill="none" stroke="#999"/></svg>April 10, 2015</span><span><svg width="12" height="11"><ellipse cx="6" cy="5" rx="5" ry="4" fill="none" stroke="#999"/></svg>Leave a comment</span></div>
    <p class="article-excerpt">As the title suggests, Module 4 of Root Reset: Adrenal Fatigue is all about lifestyle factors. Specifically, how you can make changes to your lifestyle in the areas of stress, sleep, social connection, and exercise and recovery.</p>
  </div>
  <div class="read-more">READ MORE</div>
</article>

<article class="article abs" style="top:1878px">
  <div class="article-thumb" role="img" aria-label="Orange graphic with a round emblem" style="background:#e05b2a"></div>
  <div class="article-body">
    <h3 class="article-title">What Do You Mean I Can't Have Coffee?!? – Module 2 Root Reset: Adrenal Fatigue</h3>
    <div class="article-meta"><span><svg width="11" height="11"><rect x="1" y="2" width="9" height="8" fill="none" stroke="#999"/></svg>April 10, 2015</span><span><svg width="12" height="11"><ellipse cx="6" cy="5" rx="5" ry="4" fill="none" stroke="#999"/></svg>Leave a comment</span></div>
    <p class="article-excerpt">As the title suggests, Module 4 of Root Reset: Adrenal Fatigue is all about lifestyle factors. Specifically, how you can make changes to your lifestyle in the areas of stress, sleep, social connection, and exercise and recovery.</p>
  </div>
  <div class="read-more">READ MORE</div>
</article>

<aside>
  <h2 class="sidebar-title abs" style="left:884px;top:592px">Recent Post</h2>
  <div class="recent abs" style="top:640px">
    <div class="recent-thumb" role="img" aria-label="Photo of a woman celebrating outdoors" style="background:linear-gradient(180deg,#c9dcea,#8aa7bd)"></div>
    <p>Ut enim ad minim veniam, quis nostrud exercitation ullamco laboris nisi ut aliquip ex</p>
  </div>
  <div class="recent abs" style="top:745px">
    <div class="recent-thumb" role="img" aria-label="Photo of a red apple" style="background:linear-gradient(180deg,#d84040,#8e1414)"></div>
    <p>Ut enim ad minim veniam, quis nostrud exercitation ullamco laboris nisi ut aliquip ex</p>
  </div>
  <div class="recent abs" style="top:853px">
    <div class="recent-thumb" role="img" aria-label="Photo of a smiling older couple" style="background:linear-gradient(180deg,#e8ecef,#c3cdd6)"></div>
    <p style="font-weight:600;color:#222">Ut enim ad minim veniam, quis nostrud exercitation ullamco laboris nisi ut aliquip ex</p>
  </div>
  <div class="view-all abs">VIEW ALL</div>
  <div class="rule abs"></div>

  <form class="signup abs">
    <h3>SIGN UP</h3>
    <div class="sub">FOR RIDGEWAY FERN LADY NEWSLETTER</div>
    <p class="lede">Exclusive, subscribers-only content delivered straight to your inbox</p>
    <label>Email Address</label>
    <div class="field">Enter here</div>
    <label>Enter First Name</label>
    <div class="field">Enter here</div>
    <label>Last Name</label>
    <div class="field">Enter here</div>
    <div class="submit">SUBMIT</div>
  </form>

  <h3 class="feed-title abs">Ridgeway Fern Lady on Snapfeed</h3>
  <div class="feed-grid abs">
    <div role="img" aria-label="Photo of a salad" style="background:#5f7a3e"></div>
    <div role="img" aria-label="Photo of sliced meat" style="background:#7a4a3c"></div>
    <div role="img" aria-label="Photo of a meal" style="background:#a8623a"></div>
    <div role="img" aria-label="Photo of a snack bar package" style="background:#c9c3b5"></div>
    <div role="img" aria-label="Photo of red berries" style="background:#9c2a3e"></div>
    <div role="img" aria-label="Photo of friends at an event" style="background:#6e6258"></div>
    <div role="img" aria-label="Photo of a crowd at a concert" style="background:#4a3a30"></div>
    <div role="img" aria-label="Photo of a chalkboard sign" style="background:#2e2b2a"></div>
  </div>
  <div class="feed-btn abs" style="left:884px;width:82px">Load More...</div>
  <div class="feed-btn abs" style="left:971px;width:138px">
    <svg width="10" height="10" style="vertical-align:-1px;margin-right:4px"><rect x="0.5" y="0.5" width="9" height="9" fill="none" stroke="#fff"/></svg>Follow on Snapfeed</div>

  <div class="accordion abs" style="top:1755px">Recent Comments<svg width="10" height="7"><path d="M1 1l4 4 4-4" fill="none" stroke="#fff" stroke-width="1.5"/></svg></div>
  <div class="accordion abs" style="top:1807px">Archives<svg width="10" height="7"><path d="M1 1l4 4 4-4" fill="none" stroke="#fff" stroke-width="1.5"/></svg></div>
  <div class="accordion abs" style="top:1858px">Categories<svg width="10" height="7"><path d="M1 1l4 4 4-4" fill="none" stroke="#fff" stroke-width="1.5"/></svg></div>
</aside>

<footer class="site-footer abs"></footer>
<div class="social abs" role="img" aria-label="Social profile link" style="left:77px;background:#3b5a99"></div>
<div class="social abs" role="img" aria-label="Social profile link" style="left:118px;background:#2fa3d6"></div>
<div class="social abs" role="img" aria-label="Social profile link" style="left:159px;background:#8a6f55"></div>
<div class="social abs" role="img" aria-label="Social profile link" style="left:200px;background:#c8302a"></div>
<p class="copyright abs">Copyrights 2012-2014 Yoursite All Right Reserved.</p>
<div class="footer-news abs">NEWSLETTER SIGN UP..</div>
<div class="footer-input abs">Enter your Email..</div>
<div class="footer-go abs"><svg width="34" height="32"><path d="M15 11l5 5-5 5" fill="none" stroke="#fff" stroke-width="2"/></svg></div>

</body>
</html>
```